National Mission Critical Construction Contractor needs Stationery Design to make a bold statement

We are a small commercial construction company, working primarily in mission critical facilities across the U.S.. We have exciting corporate changes going an and a new logo and office space so we need new stationery. The final design should incorporate our new logo and invoke a fresh, high-tech feel while looking simple and modern.

Industry/Entity Type

Construction

Contact Information for Business Card

We are required to list our state licensing qualifications on the back of our card.

Font styles to use
Sans Serif

Requirements
Must have
• We need to have a design for second page of stationery, envelopes both standard and with a window and for a 3 x 4 notepad.

```html
<!DOCTYPE html>
<html lang="en">
<head>
<meta charset="utf-8">
<title>Cedar Forge – Business Card</title>
<link rel="stylesheet" href="https://fonts.googleapis.com/css2?family=Open+Sans:wght@400;600&display=swap">
<style>
  :root {
    --backdrop: #3b3b3b;
    --card: #f7f7f7;
    --brand-blue: #1467b3;
    --sky-blue: #2a9fd8;
    --ink: #454545;
  }
  * { margin: 0; padding: 0; box-sizing: border-box; }
  html, body { width: 1200px; height: 750px; overflow: hidden; }
  body {
    background: var(--backdrop);
    font-family: "Open Sans", sans-serif;
    position: relative;
  }
  .card {
    position: absolute;
    top: 228px;
    width: 461px;
    height: 262px;
    background: var(--card);
    overflow: hidden;
  }
  .card--front { left: 124px; }
  .card--back { left: 618px; }

  .brand-panel {
    position: absolute;
    left: 330px; top: 0;
    width: 131px; height: 100%;
    background: var(--brand-blue);
  }
  .holder-name {
    position: absolute; left: 28px; top: 32px;
    font-size: 17px; font-weight: 600;
    color: var(--brand-blue); letter-spacing: 0.2px;
  }
  .holder-role {
    position: absolute; left: 28px; top: 53px;
    font-size: 13px; color: var(--sky-blue);
  }
  .address {
    position: absolute; left: 28px; top: 114px;
    font-size: 12.5px; line-height: 17px; color: var(--ink);
    font-style: normal;
  }
  .contacts {
    position: absolute; left: 28px; top: 152px;
    list-style: none;
  }
  .contacts li {
    display: flex; align-items: center;
    height: 17.6px;
    font-size: 12.5px; color: var(--ink);
  }
  .contacts svg {
    width: 12px; height: 12px; margin-right: 6px;
    fill: var(--brand-blue);
  }

  .wordmark {
    position: absolute; left: 0; right: 0; top: 116px;
    display: flex; justify-content: center; align-items: center;
    gap: 10px;
  }
  .wordmark-dot {
    width: 22px; height: 22px; border-radius: 50%;
    background: var(--brand-blue);
  }
  .wordmark-name {
    font-size: 25px; font-weight: 400; letter-spacing: 1px;
    color: var(--brand-blue);
  }
</style>
</head>
<body>
  <section class="card card--front">
    <div class="brand-panel"></div>
    <h1 class="holder-name">DANA REYES</h1>
    <p class="holder-role">CEO/Founder</p>
    <address class="address">4120 Alder Court<br>Fairbanks, Alaska 99701</address>
    <ul class="contacts">
      <li><svg viewBox="0 0 12 12"><path d="M2.5 1l2 2.2-1 1.3c.7 1.5 1.8 2.6 3.3 3.3l1.3-1 2.2 2-1.2 1.7C5.5 10.3 1.7 6.5 1 2.2z"/></svg>555 210 4471</li>
      <li><svg viewBox="0 0 12 12"><path d="M3 0h6v12H3zM4 1.5v8h4v-8z"/></svg>555 318 2096</li>
      <li><svg viewBox="0 0 12 12"><path d="M3 0h6v4H3zM0 5h12v5H0zM2 10h8v2H2z"/></svg>555 742 6630</li>
      <li><svg viewBox="0 0 12 12"><path d="M0 2h12v8H0zM1 3l5 3.5L11 3v-.2H1z" fill-rule="evenodd"/></svg>dana@cedarforge.com</li>
      <li><svg viewBox="0 0 12 12"><circle cx="6" cy="6" r="5.5"/></svg>www.cedarforge.com</li>
    </ul>
  </section>

  <section class="card card--back">
    <div class="wordmark">
      <span class="wordmark-dot"></span>
      <span class="wordmark-name">CEDAR FORGE</span>
    </div>
  </section>
</body>
</html>
```